Need Amazing Website for Consulting Company

We need an amazing website design for a Human Resources Consulting Company. This will be geared towards a more professional crowd, but we don't want it to be overly corporate and stuffy: Just, clean and professional and amazing. Please use the video link below for further instruction.

http://clipharbor.net/v/kLm9PxQz

Thank You.

PS Logo file has been attached.

Target Market(s)

The target marketing is small business owners who have employees. These owners cant afford an in-house HR person so they would hire this client to consult and do the work for them.

Industry/Entity Type

It Company

Font styles to use
Sans Serif

Requirements
Must have
• Please watch video:

Must have spot for video on homepage.
Nice to have
• Clean, professional, but not overly corporate, we want a personal and fun feel to this site a bit to separate them from all the other executive type sites. This site should have some LIFE to it and reflect a local brand that is doing great things.
Should not have
• Should not be just a corporate site, should not be overly stuffy, should not be overly boring.

```html
<!DOCTYPE html>
<html lang="en">
<head>
<meta charset="utf-8">
<title>Mesa Ridge HR Consulting, LLC</title>
<link href="https://fonts.googleapis.com/css2?family=Merriweather:wght@300;400;700;900&display=swap" rel="stylesheet">
<style>
:root{
  --red:#c8201f;
  --red-dark:#9f1616;
  --red-deep:#7e1010;
  --ink:#1d1d1d;
  --white:#ffffff;
  --paper:#eeeeee;
  --muted:#6d6d6d;
  --line:#d6d6d6;
}
*{margin:0;padding:0;box-sizing:border-box}
html,body{width:1200px;height:857px;overflow:hidden}
body{position:relative;background:var(--paper);font-family:"Merriweather",Georgia,serif;color:var(--ink)}

.hero-photo{position:absolute;left:0;top:0;width:1200px;height:527px;
  background:linear-gradient(100deg,#7f9bb1 0%,#a7b8c6 30%,#c3c7cb 55%,#b2a79c 75%,#8e8783 100%)}
.hero-shade{position:absolute;left:0;top:0;width:1200px;height:527px;background:linear-gradient(180deg,rgba(40,55,70,.1),rgba(30,40,55,.35))}

.topbar{position:absolute;left:0;top:0;width:1200px;height:33px;background:var(--red)}
.topbar .appointment{position:absolute;left:637px;top:11px;color:var(--white);font-size:9.6px;font-weight:700;letter-spacing:.1px;white-space:nowrap}
.topbar .contact{position:absolute;left:782px;top:0;width:128px;height:33px;background:var(--red-dark);color:var(--white);font-size:9.6px;display:flex;align-items:center;justify-content:center;gap:6px;white-space:nowrap}
.topbar .social{position:absolute;top:0;width:38px;height:33px;background:var(--red-dark);border-left:1px solid var(--red);display:flex;align-items:center;justify-content:center}
.topbar .social span{width:15px;height:15px;border-radius:50%;background:#6e0b0b}
.topbar .social.active span{background:var(--white)}

.header{position:absolute;left:0;top:33px;width:1200px;height:90px;background:rgba(255,255,255,.93)}
.brand{position:absolute;left:178px;top:28px;display:flex;align-items:center;gap:10px}
.brand-mark{width:14px;height:14px;background:var(--red)}
.brand-name{font-size:21px;font-weight:700;color:var(--ink);line-height:1.1;white-space:nowrap}
.nav{position:absolute;left:478px;top:0;height:90px;display:flex}
.nav a{display:block;height:90px;line-height:94px;font-size:10px;text-decoration:none;color:#555;text-transform:uppercase;text-align:center;white-space:nowrap}
.nav a.current{width:118px;color:var(--red);background:rgba(255,255,255,.6);border-bottom:3px solid var(--red);font-weight:700}
.nav a.about{width:160px}
.nav a.blog{width:118px}
.nav a.contact-link{width:160px}

.video{position:absolute;left:189px;top:227px;width:407px;height:195px;background:var(--red-deep);padding:6px;box-shadow:0 4px 10px rgba(0,0,0,.45)}
.video-screen{width:100%;height:100%;background:radial-gradient(ellipse at center,#1d1d1d,#0a0a0a);display:flex;align-items:center;justify-content:center}

.intro{position:absolute;left:616px;top:234px;width:380px;color:var(--white);text-shadow:0 1px 3px rgba(0,0,0,.5)}
.intro h1{font-size:29px;font-weight:900;line-height:37px;letter-spacing:-.5px;text-transform:uppercase}
.intro p{margin-top:16px;font-size:12.4px;line-height:20px;font-weight:400}

.band{position:absolute;left:0;top:527px;width:1200px;height:165px;background:linear-gradient(180deg,#b5191a,#d02222 60%,#c21e1e)}

.card{position:absolute;top:558px;width:274px;height:165px;border:2px solid #e6e6e6;box-shadow:0 3px 8px rgba(0,0,0,.3)}
.card.team{left:184px;background:linear-gradient(135deg,#e9ecef,#b9bec3 50%,#7a7f86)}
.card.target{left:464px;background:radial-gradient(circle at 55% 50%,#d8b43c 0,#b0891f 22%,#8b8e92 45%,#a9acb0 100%)}
.card.feature{left:744px;border-color:#8c8c8c;background:#3a3b3d;color:var(--white);text-align:center;padding:30px 24px 0}
.card.feature h2{font-size:13px;font-weight:700;margin-top:8px}
.card.feature p{font-size:9.5px;line-height:16px;font-weight:300;margin-top:7px}

.divider{position:absolute;left:171px;top:758px;width:858px;height:1px;background:var(--line)}
.copyright{position:absolute;left:179px;top:802px;font-size:11px;color:var(--muted)}
.footer-social{position:absolute;top:799px;width:17px;height:17px;border-radius:50%;background:#8a8a8a}
.footer-social.active{background:#fdfdfd;box-shadow:0 0 0 1px #ccc}
</style>
</head>
<body>
  <div class="hero-photo" role="img" aria-label="Photo of a cheerful business team celebrating in an office"></div>
  <div class="hero-shade"></div>

  <div class="topbar">
    <span class="appointment">MAKE AN APPOINTMENT</span>
    <div class="contact">
      <svg width="12" height="12" viewBox="0 0 12 12"><path d="M2 1h3l1 3-2 1a7 7 0 0 0 3 3l1-2 3 1v3a1 1 0 0 1-1 1A10 10 0 0 1 1 2a1 1 0 0 1 1-1z" fill="#fff"/></svg>
      CONTACT US
      <svg width="8" height="5" viewBox="0 0 8 5"><path d="M0 0h8L4 5z" fill="#fff"/></svg>
    </div>
    <div class="social" style="left:910px"><span></span></div>
    <div class="social active" style="left:949px"><span></span></div>
    <div class="social" style="left:988px"><span></span></div>
  </div>

  <header class="header">
    <div class="brand">
      <span class="brand-mark"></span>
      <span class="brand-name">Mesa Ridge HR</span>
    </div>
    <nav class="nav">
      <a class="current" href="#">Home</a>
      <a class="about" href="#">About Us</a>
      <a class="blog" href="#">Blog</a>
      <a class="contact-link" href="#">Contact Us</a>
    </nav>
  </header>

  <div class="video">
    <div class="video-screen" role="img" aria-label="Introductory video about people, training and rewards">
      <svg width="56" height="56" viewBox="0 0 56 56"><circle cx="28" cy="28" r="27" fill="#c8201f"/><path d="M22 17l17 11-17 11z" fill="#fff"/></svg>
    </div>
  </div>

  <section class="intro">
    <h1>Mesa Ridge HR Consulting, LLC</h1>
    <p>(MRHC) is an experienced consulting agency that is committed to providing businesses with effective and efficient Human Resources support by developing partnerships to meet company's individual needs.</p>
  </section>

  <div class="band"></div>

  <div class="card team" role="img" aria-label="Photo of a group of business professionals walking together"></div>
  <div class="card target" role="img" aria-label="Illustration of a magnifying glass over a target among small figures"></div>
  <div class="card feature">
    <svg width="24" height="24" viewBox="0 0 24 24"><path d="M10 0h4v10h10v4H14v10h-4V14H0v-4h10z" fill="#fff"/></svg>
    <h2>Lorem ipsum dolor</h2>
    <p>(MRHC) is an experienced consulting agency that is committed to providing businesses with effective and efficient Human Resources .</p>
  </div>

  <div class="divider"></div>
  <footer>
    <p class="copyright">Copyright © 2014 Mesa Ridge HR Consulting, LLC. All Rights Reserved.</p>
    <span class="footer-social" style="left:929px"></span>
    <span class="footer-social active" style="left:968px"></span>
    <span class="footer-social" style="left:1006px"></span>
  </footer>
</body>
</html>
```